American cannabis tech company business card design

Pavrel.com is seeking a modern, professional, and brand-aligned business card that represents our company and its core values: Mission, Story, Values, and Impact. As an innovative cannabis company, we want a business card that is not only visually appealing but also serves as a representation of who we are and what we stand for.

Project Scope: Design a double-sided business card that integrates our brand identity and core values. Incorporate our key brand elements, ensuring a sleek and contemporary aesthetic. Visually reflect our core values (Mission, Story, Values, Impact) in a way that is engaging yet professional.

Target Market(s)

Vendors, third parties,

Contact Information for Business Card

Contact details (name, title, email, phone, website, etc.)

Font styles to use
Other font styles liked:
• Caslon, Centra

Colors

Designer to choose colors to be used in the design.

Requirements
Must have
• Pavrel.com logo and branding A creative yet clean way to integrate our core values (Mission, Story, Values, Impact) Modern typography and a well-structured layout
Nice to have
• forest green, grey, white, black
Should not have
• references to marijuana, leafs, plants, or related product

```html
<!DOCTYPE html>
<html lang="en">
<head>
<meta charset="UTF-8">
<title>Pavrel.com Business Card</title>
<link href="https://fonts.googleapis.com/css2?family=Poppins:wght@400;600;700;800&display=swap" rel="stylesheet">
<style>
  :root {
    --forest: #1a3a1d;
    --forest-deep: #15301a;
    --paper: #ffffff;
    --ink: #1a3a1d;
    --stage: #3b3b3b;
    --rule: #b9b9b9;
  }
  * { box-sizing: border-box; margin: 0; padding: 0; }
  html, body { width: 1200px; height: 689px; overflow: hidden; }
  body {
    background: var(--stage);
    font-family: "Poppins", sans-serif;
    position: relative;
  }
  .card {
    position: absolute;
    top: 195px;
    width: 520px;
    height: 300px;
    border-radius: 22px;
    overflow: hidden;
  }
  .card--front {
    left: 50px;
    background: var(--forest);
    display: flex;
    align-items: center;
    justify-content: center;
  }
  .card--back {
    left: 630px;
    background: var(--paper);
  }
  .wordmark {
    font-family: "Poppins", sans-serif;
    font-weight: 800;
    font-size: 64px;
    letter-spacing: 1px;
    line-height: 1;
  }
  .card--front .wordmark { color: #e9e9e9; }
  .card--back .wordmark {
    position: absolute;
    left: 42px;
    top: 118px;
    font-size: 50px;
    color: var(--ink);
  }
  .divider {
    position: absolute;
    left: 262px;
    top: 52px;
    width: 1px;
    height: 170px;
    background: linear-gradient(to bottom, transparent, var(--rule) 25%, var(--rule) 75%, transparent);
  }
  .contact {
    position: absolute;
    left: 290px;
    top: 62px;
    color: var(--ink);
  }
  .contact__name {
    font-weight: 700;
    font-size: 19px;
    letter-spacing: 0.3px;
    line-height: 1.1;
  }
  .contact__title {
    font-weight: 400;
    font-size: 13px;
    color: #2b2b2b;
    margin-bottom: 22px;
  }
  .contact__list { list-style: none; }
  .contact__item {
    display: flex;
    align-items: center;
    gap: 7px;
    font-size: 13px;
    color: #2b2b2b;
    margin-bottom: 6px;
  }
  .contact__icon {
    width: 18px;
    height: 18px;
    flex: none;
  }
  .band {
    position: absolute;
    left: 0;
    bottom: 0;
    width: 100%;
    height: 34px;
    background: var(--forest);
  }
  .band::before {
    content: "";
    position: absolute;
    left: 0;
    top: 4px;
    width: 100%;
    height: 1.5px;
    background: var(--paper);
  }
</style>
</head>
<body>
  <section class="card card--front" aria-label="Card front">
    <span class="wordmark">PAVREL</span>
  </section>

  <section class="card card--back" aria-label="Card back">
    <span class="wordmark">PAVREL</span>
    <div class="divider"></div>
    <div class="contact">
      <p class="contact__name">DANIEL HARTLEY</p>
      <p class="contact__title">Managing Director</p>
      <ul class="contact__list">
        <li class="contact__item">
          <svg class="contact__icon" viewBox="0 0 18 18"><circle cx="9" cy="9" r="9" fill="#1a3a1d"/><path d="M6.2 4.8l1.4 1.6-.8 1.2c.6 1.3 1.5 2.2 2.8 2.8l1.2-.8 1.6 1.4-.9 1.4c-3.2-.3-6-3.1-6.3-6.3z" fill="#fff"/></svg>
          <span>044-555 210 478</span>
        </li>
        <li class="contact__item">
          <svg class="contact__icon" viewBox="0 0 18 18"><circle cx="9" cy="9" r="9" fill="#1a3a1d"/><rect x="4.5" y="6" width="9" height="6.5" fill="none" stroke="#fff" stroke-width="1.1"/><path d="M4.5 6l4.5 3.6L13.5 6" fill="none" stroke="#fff" stroke-width="1.1"/></svg>
          <span>info@pavrel.com</span>
        </li>
        <li class="contact__item">
          <svg class="contact__icon" viewBox="0 0 18 18"><circle cx="9" cy="9" r="9" fill="#1a3a1d"/><g fill="none" stroke="#fff" stroke-width="1"><circle cx="9" cy="9" r="4.6"/><ellipse cx="9" cy="9" rx="2" ry="4.6"/><path d="M4.4 9h9.2"/></g></svg>
          <span>www.pavrel.com</span>
        </li>
      </ul>
    </div>
    <div class="band"></div>
  </section>
</body>
</html>
```